Cyber Security firm working in the Financial Services sector needs a brochure

We need a brochure covering our products and offerings. We work exclusively with Independent Broker Dealers, their Reps and RIAs in the US. We help them keep their computers secure and compliant with applicable regulations and policies. Have attached samples of our logo an descriptions of our products and services.

Target Market(s)

Financial Institutions and Financial Advisors

Industry/Entity Type

Financial Service

```html
<!DOCTYPE html>
<html lang="en">
<head>
<meta charset="utf-8">
<title>Vaultline Secure – Cyber Security Solutions</title>
<link rel="stylesheet" href="https://fonts.googleapis.com/css2?family=Open+Sans:wght@400;600&family=Ubuntu:wght@500;700&display=swap">
<style>
  :root {
    --backdrop: #e9e9e9;
    --paper: #ffffff;
    --navy: #0b1f5e;
    --navy-deep: #06123c;
    --brand-blue: #1a4aa3;
    --sky: #2f8fe0;
    --sky-light: #56b4f2;
    --intro-band: #dde4ec;
    --body-text: #5a5f66;
  }
  * { box-sizing: border-box; margin: 0; padding: 0; }
  html, body {
    width: 1200px; height: 960px; overflow: hidden;
    background: var(--backdrop);
  }
  .flyer {
    position: absolute; left: 250px; top: 27px;
    width: 700px; height: 906px;
    background: var(--paper);
    box-shadow: 0 6px 22px rgba(0,0,0,.12);
    overflow: hidden;
    font-family: "Open Sans", Arial, sans-serif;
    color: var(--body-text);
  }
  .brand-name {
    position: absolute; left: 34px; top: 24px;
    font-family: "Ubuntu", Arial, sans-serif; font-weight: 700;
    font-size: 19px; color: var(--brand-blue);
    display: flex; align-items: center; gap: 8px;
  }
  .brand-name .mark {
    width: 12px; height: 12px; border-radius: 50%; background: var(--brand-blue);
  }
  .banner { position: absolute; left: 0; top: 62px; width: 700px; height: 250px; }
  .banner-title {
    position: absolute; left: 0; top: 162px; width: 700px; text-align: center;
    font-family: "Ubuntu", Arial, sans-serif; font-weight: 700;
    font-size: 32px; letter-spacing: .5px; color: #fff;
    text-shadow: 0 2px 6px rgba(0,0,0,.45);
  }
  .intro {
    position: absolute; left: 0; top: 312px; width: 700px; height: 94px;
    background: var(--intro-band);
    padding: 20px 44px;
    font-size: 10px; line-height: 1.45;
  }
  .service h2 {
    font-family: "Ubuntu", Arial, sans-serif; font-weight: 700;
    font-size: 16px; color: var(--brand-blue); text-transform: uppercase;
    margin-bottom: 5px;
  }
  .service p { font-size: 8.8px; line-height: 1.42; }
  .service { position: absolute; }
  .backup { left: 44px; top: 424px; width: 612px; }
  .antivirus { left: 44px; top: 510px; width: 612px; }
  .patching { left: 44px; top: 628px; width: 350px; }
  .encryption { left: 430px; top: 628px; width: 226px; }
  .footer { position: absolute; left: 0; bottom: 0; width: 700px; height: 84px; }
  .footer-url {
    position: absolute; left: 392px; bottom: 22px;
    font-family: "Ubuntu", Arial, sans-serif; font-weight: 500;
    font-size: 12px; color: #fff; letter-spacing: .3px;
  }
  .footer-brand {
    position: absolute; right: 24px; bottom: 26px;
    font-family: "Ubuntu", Arial, sans-serif; font-weight: 700;
    font-size: 13px; color: var(--brand-blue);
  }
</style>
</head>
<body>
<article class="flyer">
  <div class="brand-name"><span class="mark"></span>Vaultline Secure</div>

  <svg class="banner" viewBox="0 0 700 250" aria-hidden="false">
    <defs>
      <radialGradient id="tunnel-glow" cx="50%" cy="45%" r="60%">
        <stop offset="0" stop-color="#bfe6ff"/>
        <stop offset=".25" stop-color="#2a78d0"/>
        <stop offset=".7" stop-color="#0d2770"/>
        <stop offset="1" stop-color="#06123c"/>
      </radialGradient>
    </defs>
    <polygon points="0,20 150,20 170,0 560,0 580,20 700,20 700,215 0,215" fill="#0b1f5e"/>
    <rect x="0" y="28" width="700" height="180" fill="url(#tunnel-glow)" role="img"
          aria-label="Digital tunnel of binary code lined with computer monitors"/>
    <polygon points="0,20 148,20 168,0 300,0 292,10 174,10 156,30 0,30" fill="#2f8fe0"/>
    <polygon points="700,20 582,20 562,0 420,0 428,10 556,10 574,30 700,30" fill="#2f8fe0"/>
    <polygon points="0,208 700,208 700,226 0,226" fill="#56b4f2"/>
    <polygon points="0,226 190,226 176,250 0,250" fill="#1a4aa3"/>
    <polygon points="700,226 520,226 534,250 700,250" fill="#1a4aa3"/>
  </svg>
  <h1 class="banner-title">CYBER SECURITY SOLUTIONS</h1>

  <p class="intro">Vaultline Secure provides Computer Security support and services to the Broker Dealer and Independent Advisor community. We have been providing these services for over eight years and our team has decades of experience in the Financial Services sector. We currently support, monitor and inspect thousands of Advisors and their devices across multiple Broker Dealers and RIAs. Below is a list of our most popular services.</p>

  <section class="service backup">
    <h2>Managed Backup</h2>
    <p>We partner with Northvale owned Cloudkeep Pro to provide backup services. This provides encrypted transmission and storage in SSAE 16 audited and ISO 27001 certified facilities for your back-up needs. We help you configure the back-ups, monitor them on a daily basis and are there to help if you need to do any restores. Price $1 per GB per month.</p>
  </section>

  <section class="service antivirus">
    <h2>Managed Anti-Virus</h2>
    <p>Correctly functioning and up-to-date Anti-Virus (AV) software is a requirement for all computers connected to the internet. With only one or two computers it is relatively easy to stay on top of the situation. However, once you get more than a couple of computers and users knowing their condition becomes more difficult without centralized reporting and monitoring. Our managed AV solution provides a centralized portal for monitoring and reporting. We are notified of any issues, whether it's a virus detected or an issue with the AV itself. This software and service is available for $52 per user per year with a one time set up fee of $25 per device. The advantage of the per user fee is, if a user has both a desktop and a laptop, both will be covered for the $52 per year.</p>
  </section>

  <section class="service patching">
    <h2>Managed Software Patching</h2>
    <p>Keeping computers up-to-date with all critical security patches is an important component in protecting your infrastructure. An effective Patch Management strategy requires timely application of patches. Our patching functions in a closed loop environment. We push the necessary patches to the computers and then use our monitoring system at the device level to verify all have been successfully applied. This solution is quite effective for distributed environments with limited local cyber security expertise as well as small offices which prefer to outsource this requirement. Price $3.99 per month per computer. Requires Computer Security Monitoring.</p>
  </section>

  <section class="service encryption">
    <h2>Whole Disk Encryption</h2>
    <p>We remotely access your computer and perform whole disk encryption as required by your Broker Dealer. We can also help you select the most appropriate encryption methodology for your specific environment. Pricing from $95 per computer.</p>
  </section>

  <footer class="footer">
    <svg width="700" height="84" viewBox="0 0 700 84" aria-hidden="true">
      <polygon points="340,84 372,40 700,40 700,84" fill="#1a4aa3"/>
      <polygon points="322,84 354,40 366,40 334,84" fill="#56b4f2"/>
      <polygon points="580,40 596,24 700,24 700,40" fill="#ffffff"/>
    </svg>
    <span class="footer-url">www.vaultlinesecure.com</span>
  </footer>
</article>
</body>
</html>
```